Email Signature and a letter head

I need a professional email signature and a letter head for letters sent by post. I've attached my logo and a signature i am currently using. Current letter head is also attached.

Target Market(s)

Accounting Clients

Industry/Entity Type

Public Accounting

Font styles to use
Sans Serif

Colors

Designer to choose colors to be used in the design.

Requirements
Must have
• My logo, RM Logo, Lumo Logo, Tax Agent logo. All attached.
• All my credentials - examples in the attached documents

```html
<!DOCTYPE html>
<html lang="en">
<head>
<meta charset="utf-8">
<title>Summit to Shore – Letterhead and Email Signature</title>
<link href="https://fonts.googleapis.com/css2?family=Cinzel:wght@400;500&family=Tinos:wght@400;700&family=Open+Sans:wght@400;600&display=swap" rel="stylesheet">
<style>
:root{
  --gold:#a88a2a;
  --dark:#2f2f2f;
  --paper:#f8f8f8;
  --white:#ffffff;
  --stage:#b2b2b2;
  --ink:#333333;
  --faint:#ececec;
  --rule:#d6d6d6;
  --navy:#2d3a6b;
  --green:#2f9a3a;
  --lumo-light:#1aa6d6;
  --lumo-dark:#0e6f8a;
  --badge-red:#d0402f;
  --badge-lime:#b8cc2a;
}
*{box-sizing:border-box;margin:0;padding:0}
html,body{width:1200px;height:872px;overflow:hidden;background:var(--stage)}
.canvas{position:relative;width:1200px;height:872px}
.serif{font-family:"Tinos","Times New Roman",serif}
.brand{font-family:"Cinzel","Times New Roman",serif}

/* Letterhead */
.letterhead{position:absolute;left:182px;top:145px;width:412px;height:581px;background:var(--paper);overflow:hidden}
.letterhead .shapes{position:absolute;inset:0}
.lh-logo{position:absolute;right:18px;top:22px;text-align:center;width:150px}
.logo-dot{display:block;margin:0 auto 6px;width:54px;height:54px;border:2px solid var(--gold);border-radius:50%}
.logo-name{color:var(--gold);font-size:14px;letter-spacing:.5px;line-height:1}
.logo-sub{color:var(--gold);font-size:6.5px;letter-spacing:2px;margin-top:3px}
.lh-contact{position:absolute;left:17px;top:493px;color:var(--ink)}
.person{font-family:"Tinos",serif;color:var(--gold);font-size:14px;font-weight:700;letter-spacing:.2px}
.creds{font-size:7.5px;margin-top:2px}
.creds b{color:var(--gold);font-weight:400}
.creds .sep{color:var(--gold);margin:0 4px}
.lines{list-style:none;margin-top:9px;font-size:7.8px;line-height:8.5px}
.lines li{display:flex;align-items:center;gap:5px}
.lines svg{width:6px;height:6px;flex:none}
.partners{position:absolute;display:flex;align-items:center}
.lumo{display:flex;align-items:center;gap:3px}
.lumo-dot{border-radius:50%;background:var(--lumo-light)}
.lumo-name{font-family:"Tinos",serif;color:var(--lumo-dark);font-weight:700}
.plain-badge{border-radius:50%}
.tax{font-family:"Open Sans",sans-serif;font-weight:600;color:var(--dark);line-height:1.05}

/* Email signature */
.email{position:absolute;left:618px;top:380px;width:400px;height:215px;background:var(--white)}
.sig{position:absolute;left:15px;top:14px;width:370px;height:90px;border:1px solid var(--rule);background:var(--white);overflow:hidden}
.sig-logo{position:absolute;left:6px;top:12px;width:130px;text-align:center}
.sig-logo .logo-dot{width:38px;height:38px;margin-bottom:4px;border-width:1.6px}
.sig-logo .logo-name{font-size:9.5px}
.sig-logo .logo-sub{font-size:4.6px;letter-spacing:1.4px;margin-top:1px}
.sig-divider{position:absolute;left:146px;top:12px;width:1.5px;height:52px;background:var(--gold)}
.sig-info{position:absolute;left:156px;top:12px;color:var(--ink)}
.sig-info .person{font-size:11px}
.sig-info .creds{font-size:6px;margin-top:0}
.sig-info .lines{font-size:6px;line-height:7.2px;margin-top:5px}
.sig-info .lines svg{width:5px;height:5px}
.sig-band{position:absolute;left:0;bottom:0;width:100%;height:10px}
.tagline{position:absolute;left:12px;bottom:1.5px;font-family:"Open Sans",sans-serif;font-size:5.4px;color:var(--white)}
.disclaimer{position:absolute;left:17px;top:110px;width:360px;font-family:"Open Sans",sans-serif;font-size:5.2px;line-height:7px;color:var(--navy)}
.eco{position:absolute;left:26px;top:137px;display:flex;align-items:center;gap:22px;font-family:"Open Sans",sans-serif;font-size:5.4px;color:var(--green)}
.eco-mark{width:13px;height:12px;background:var(--green);border-radius:2px}
</style>
</head>
<body>
<main class="canvas">

  <!-- Printed letterhead -->
  <section class="letterhead" aria-label="Letterhead">
    <svg class="shapes" width="412" height="581" viewBox="0 0 412 581">
      <polygon points="0,0 316,0 0,14" fill="var(--gold)"/>
      <polygon points="0,14 316,0 0,18" fill="var(--dark)"/>
      <circle cx="206" cy="300" r="146" fill="none" stroke="var(--faint)" stroke-width="5"/>
      <rect x="0" y="563" width="233" height="2.5" fill="var(--gold)"/>
    </svg>

    <div class="lh-logo">
      <span class="logo-dot"></span>
      <div class="logo-name brand">Summit to Shore</div>
      <div class="logo-sub brand">Business Services</div>
    </div>

    <div class="lh-contact serif">
      <div class="person">Delphine Marsh RM BBus.</div>
      <div class="creds"><b>ABN:</b> 41 208 377 516<span class="sep">|</span><b>TAN:</b> 318 402 77</div>
      <ul class="lines">
        <li><svg viewBox="0 0 10 10"><path d="M2 1h2l1 3-1.5 1a6 6 0 0 0 2.5 2.5L7 6l3 1v2c-5 1-10-4-8-8z" fill="var(--ink)"/></svg>0412555708</li>
        <li><svg viewBox="0 0 10 10"><circle cx="5" cy="5" r="4" fill="none" stroke="var(--ink)"/><path d="M1 5h8M5 1v8" stroke="var(--ink)"/></svg>www.summittoshorebusiness.com.au</li>
        <li><svg viewBox="0 0 10 10"><rect x="1" y="2" width="8" height="6" fill="var(--ink)"/><path d="M1 2l4 3 4-3" stroke="var(--white)" fill="none"/></svg>delphine@summittoshorebusiness.com.au</li>
        <li><svg viewBox="0 0 10 10"><path d="M5 10C2 6 2 5 2 4a3 3 0 0 1 6 0c0 1 0 2-3 6z" fill="var(--ink)"/><circle cx="5" cy="4" r="1" fill="var(--white)"/></svg>18 Harbour Lane Seaview VIC 3999</li>
      </ul>
    </div>

    <div class="partners" style="left:240px;top:532px;gap:10px">
      <div class="lumo"><span class="lumo-dot" style="width:25px;height:25px"></span><span class="lumo-name" style="font-size:10px">Lumo</span></div>
      <span class="plain-badge" role="img" aria-label="Professional body badge" style="width:22px;height:22px;background:var(--badge-red)"></span>
      <span class="plain-badge" role="img" aria-label="Registered tax agent badge" style="width:24px;height:24px;background:var(--badge-lime)"></span>
      <span class="tax" style="font-size:5.5px">Tax Agent<br>31840277</span>
    </div>
  </section>

  <!-- Email signature -->
  <section class="email" aria-label="Email signature">
    <div class="sig">
      <div class="sig-logo">
        <span class="logo-dot"></span>
        <div class="logo-name brand">Summit to Shore</div>
        <div class="logo-sub brand">Business Services</div>
      </div>
      <div class="sig-divider"></div>
      <div class="sig-info serif">
        <div class="person">Delphine Marsh RM BBus.</div>
        <div class="creds"><b>ABN:</b> 41 208 377 516<span class="sep">|</span><b>TAN:</b> 318 402 77</div>
        <ul class="lines">
          <li><svg viewBox="0 0 10 10"><path d="M2 1h2l1 3-1.5 1a6 6 0 0 0 2.5 2.5L7 6l3 1v2c-5 1-10-4-8-8z" fill="var(--ink)"/></svg>0412555708</li>
          <li><svg viewBox="0 0 10 10"><circle cx="5" cy="5" r="4" fill="none" stroke="var(--ink)"/><path d="M1 5h8M5 1v8" stroke="var(--ink)"/></svg>www.summittoshorebusiness.com.au</li>
          <li><svg viewBox="0 0 10 10"><rect x="1" y="2" width="8" height="6" fill="var(--ink)"/><path d="M1 2l4 3 4-3" stroke="var(--white)" fill="none"/></svg>delphine@summittoshorebusiness.com.au</li>
          <li><svg viewBox="0 0 10 10"><path d="M5 10C2 6 2 5 2 4a3 3 0 0 1 6 0c0 1 0 2-3 6z" fill="var(--ink)"/><circle cx="5" cy="4" r="1" fill="var(--white)"/></svg>18 Harbour Lane Seaview VIC 3999</li>
        </ul>
      </div>
      <div class="partners" style="right:6px;top:14px;flex-direction:column;align-items:center;gap:5px">
        <div class="lumo"><span class="lumo-dot" style="width:16px;height:16px"></span><span class="lumo-name" style="font-size:7px">Lumo</span></div>
        <span class="plain-badge" role="img" aria-label="Professional body badge" style="width:13px;height:13px;background:var(--badge-red)"></span>
        <div style="display:flex;align-items:center;gap:3px">
          <span class="plain-badge" role="img" aria-label="Registered tax agent badge" style="width:15px;height:15px;background:var(--badge-lime)"></span>
          <span class="tax" style="font-size:3.8px">Tax Agent<br>31840277</span>
        </div>
      </div>
      <svg class="sig-band" viewBox="0 0 370 10" preserveAspectRatio="none">
        <rect x="0" y="3" width="370" height="7" fill="var(--dark)"/>
        <polygon points="0,0 158,0 168,10 0,10" fill="var(--gold)"/>
      </svg>
      <span class="tagline">Balance is the key of everything in life</span>
    </div>
    <p class="disclaimer">This e-mail and its attachments are confidential and privileged. Any unauthorised use is expressly prohibited. If you receive this e-mail in error please contact us, then delete the e-mail.</p>
    <div class="eco">
      <span class="eco-mark" role="img" aria-label="Small environment printer icon"></span>
      <span>Please consider the environment before printing this e-mail notice.</span>
    </div>
  </section>

</main>
</body>
</html>
```